Heron Haulage needs Bussiness cards!

Our new trucking company needs business cards!
We need the same design with two different names and emails, everything else it's the same.
I have included our original logo so we can use it for the design.
Note: the logo to be used is the o e with the buffalo on the right side, next to the letters H and H.

Target Market(s)

Trucking, refrigerated transportation, freight

Industry/Entity Type

Business

Contact Information for Business Card

Card #1:
Marcus Whitfield
marcuswhitfield@heronhaulage.example
1-855-317-6094
(956)238-7160
4117 W. Larkin Ave.
Pharr, TX 78590
www.heronhaulage.example

Card#2:
Rosalba Quintero
rosalba@heronhaulage.example
1-855-317-6094
(956)238-7160
4117 W. Larkin Ave.
Pharr, TX 78590
www.heronhaulage.example

Font styles to use
Sans Serif

Colors
0655a3
ec1f27
ffffff

Requirements
Must have
• our logo
Nice to have
• roads on background,

```html
<!DOCTYPE html>
<html lang="en">
<head>
<meta charset="utf-8">
<title>Heron Haulage – Business Card Back</title>
<link rel="stylesheet" href="https://fonts.googleapis.com/css2?family=Arimo:wght@400;700&display=swap">
<style>
  :root {
    --brand-red: #ec1f27;
    --brand-blue: #0655a3;
    --brand-navy: #0b2f5c;
    --paper: #ffffff;
    --crop-mark: #222222;
    --safe-line: #3aa6d8;
    --trim-line: #2e9e6a;
  }
  html, body {
    margin: 0;
    padding: 0;
    width: 1200px;
    height: 782px;
    overflow: hidden;
    background: var(--paper);
  }
  .print-sheet {
    display: block;
    width: 1200px;
    height: 782px;
  }
  .crop-mark { stroke: var(--crop-mark); stroke-width: 1.5; fill: none; }
  .card-face { fill: var(--brand-red); }
  .safe-guide { stroke: var(--safe-line); stroke-width: 1.2; fill: none; }
  .trim-guide { stroke: var(--trim-line); stroke-width: 1.2; fill: none; }
  .tab-slot { fill: var(--paper); }
  .wave-stripe { fill: var(--paper); }
  .wave-base { fill: var(--brand-blue); }
  .brand-mark { fill: var(--brand-navy); }
  .brand-name {
    font-family: "Arimo", Arial, sans-serif;
    font-weight: 700;
    font-size: 72px;
    fill: var(--brand-navy);
  }
  .web-address {
    font-family: "Arimo", Arial, sans-serif;
    font-weight: 400;
    font-size: 52px;
    fill: var(--paper);
  }
</style>
</head>
<body>
<svg class="print-sheet" viewBox="0 0 1184 771" preserveAspectRatio="none" xmlns="http://www.w3.org/2000/svg">
  <!-- crop marks -->
  <g class="crop-marks">
    <line class="crop-mark" x1="72" y1="0" x2="72" y2="37"/>
    <line class="crop-mark" x1="1112" y1="0" x2="1112" y2="37"/>
    <line class="crop-mark" x1="72" y1="735" x2="72" y2="771"/>
    <line class="crop-mark" x1="1112" y1="735" x2="1112" y2="771"/>
    <line class="crop-mark" x1="0" y1="72" x2="36" y2="72"/>
    <line class="crop-mark" x1="1148" y1="72" x2="1184" y2="72"/>
    <line class="crop-mark" x1="0" y1="700" x2="36" y2="700"/>
    <line class="crop-mark" x1="1148" y1="700" x2="1184" y2="700"/>
    <line class="crop-mark" x1="72" y1="0" x2="72" y2="771" opacity="0"/>
  </g>

  <!-- card with bleed -->
  <rect class="card-face" x="36" y="37" width="1112" height="698"/>
  <rect class="safe-guide" x="72" y="72" width="1040" height="628"/>
  <rect class="trim-guide" x="96" y="96" width="992" height="580"/>

  <!-- die-cut tab -->
  <rect class="tab-slot" x="1023" y="270" width="90" height="240"/>

  <!-- bottom wave -->
  <path class="wave-stripe" d="M36 578 C120 640 260 660 420 630 C620 590 860 530 1040 552 C1100 560 1130 572 1148 582 L1148 735 L36 735 Z"/>
  <path class="wave-base" d="M36 620 C130 665 260 668 430 645 C640 615 880 575 1060 590 C1110 595 1135 605 1148 618 L1148 735 L36 735 Z"/>

  <!-- brand name -->
  <g class="brand-lockup">
    <rect class="brand-mark" x="300" y="318" width="56" height="56"/>
    <text class="brand-name" x="376" y="372">Heron Haulage</text>
  </g>

  <!-- web address -->
  <text class="web-address" x="437" y="690">www.heronhaulage.example</text>
</svg>
</body>
</html>
```